Website for a new t-shirt company called bolddawnapperal.com

We are looking for a talented web designer to create a website that aligns with our brand's message and identity centered around the theme of "Bold Dawn." The website should be modern, clean, and visually appealing while also being user-friendly and easy to navigate.

We will be using the Big Commerce platform for our online store section, so the designer should have experience in designing websites on this platform.

We would like the website to have the following elements:

A color scheme that aligns with the brand's identity and message
A homepage that showcases our products and message, with clear calls-to-action for visitors to explore further
A blog section that highlights our brand's philosophy and offers advice and tips for people looking to make positive changes in their lives
An "About Us" section that introduces our brand and team and offers insight into our mission and values
A contact form that allows visitors to easily get in touch with us for inquiries or support
We are open to creative suggestions and ideas from the designer, but we would like the website to have a modern and minimalist aesthetic that resonates with our target audience of 20 to 40-year-olds.

```html
<!DOCTYPE html>
<html lang="en">
<head>
<meta charset="utf-8">
<title>Bold Dawn Apparel</title>
<link rel="stylesheet" href="https://fonts.googleapis.com/css2?family=Lato:wght@300;400;700;900&family=Poppins:wght@300;400;500&display=swap">
<style>
:root{
  --ink:#1e1e1e;
  --dark:#2b2b2b;
  --bar:#3a3a3a;
  --btn:#444444;
  --panel:#efefef;
  --card:#f2f2f2;
  --line:#d6d6d6;
  --muted:#555555;
  --gold:#f2b01e;
  --badge:#8b8b8b;
  --white:#ffffff;
}
*{box-sizing:border-box;margin:0;padding:0}
html,body{width:1200px;height:5177px;overflow:hidden}
body{position:relative;background:var(--white);font-family:"Poppins",sans-serif;color:var(--ink)}
.abs{position:absolute}
.sans{font-family:"Lato",sans-serif}

.topbar{left:0;top:0;width:1200px;height:54px;background:var(--bar);color:var(--white);font:700 13px "Lato",sans-serif;display:flex;align-items:center;justify-content:space-between;padding:0 74px}
.brand{left:74px;top:80px;font:700 40px "Lato",sans-serif;color:var(--ink);letter-spacing:-0.5px}
.nav{left:458px;top:108px;display:flex;gap:40px;font:700 13px "Lato",sans-serif;color:var(--ink)}
.icon-btn{top:92px;width:45px;height:45px;display:flex;align-items:center;justify-content:center}
.icon-btn.outline{border:2px solid var(--ink);background:var(--white)}
.icon-btn.solid{background:var(--dark)}
.hero{left:0;top:171px;width:1200px;height:655px;background:linear-gradient(90deg,#8d929b 0%,#7d828b 40%,#4a4d52 75%,#2e3033 100%)}
.hero-name{left:80px;top:318px;font:300 104px "Lato",sans-serif;color:var(--white);letter-spacing:-2px}
.hero-sub{left:84px;top:496px;font:900 54px "Lato",sans-serif;color:var(--white)}
.hero-copy{left:74px;top:562px;font:700 22px/34px "Lato",sans-serif;color:var(--white)}
.btn{display:flex;align-items:center;justify-content:center;background:var(--btn);color:var(--white);font:700 16px "Lato",sans-serif;letter-spacing:.5px}
.dot{top:768px;width:10px;height:10px;border-radius:50%;background:rgba(255,255,255,.7)}
.cat{top:854px;width:342px;height:262px;background:var(--card)}
.cat-img{position:absolute;left:20px;top:20px;width:150px;height:222px;border-radius:6px}
.cat-title{position:absolute;left:182px;top:84px;font:900 23px/28px "Lato",sans-serif}
.cat-link{position:absolute;left:182px;top:150px;font:700 12px "Lato",sans-serif;text-decoration:underline}
.mv{top:1176px;width:519px;height:305px;background:var(--dark);color:var(--white);text-align:center;padding:58px 22px 0}
.mv h2{font:700 31px "Lato",sans-serif;letter-spacing:1px;margin-bottom:16px}
.mv p{font:400 16px/33px "Poppins",sans-serif}
.about{left:74px;top:1493px;width:1052px;height:489px;background:var(--panel)}
.about h2{position:absolute;left:36px;top:66px;font:900 31px "Lato",sans-serif;letter-spacing:.5px}
.about p{position:absolute;left:36px;top:122px;width:490px;font:400 16px/33.5px "Poppins",sans-serif;color:#333}
.about .btn{position:absolute;left:36px;top:374px;width:159px;height:46px}
.about-mark{position:absolute;left:548px;top:158px;font:700 92px "Lato",sans-serif;color:var(--dark);letter-spacing:-3px;white-space:nowrap}
.sec-title{left:0;width:1200px;text-align:center;font:900 32px "Lato",sans-serif;letter-spacing:.5px}
.rule{left:74px;width:1052px;height:2px;background:var(--line)}
.prod{top:2128px;width:243px;text-align:center}
.prod-img{width:243px;height:282px;background:var(--card);position:relative}
.prod-img .shape{position:absolute;left:42px;top:36px;width:160px;height:210px;border-radius:10px}
.sale{position:absolute;right:20px;top:14px;width:64px;height:64px;border-radius:50%;background:var(--badge);color:var(--white);font:700 13px/64px "Lato",sans-serif}
.prod-name{margin-top:28px;font:900 14.5px "Lato",sans-serif}
.prod-sub{margin-top:4px;font:400 13px "Poppins",sans-serif;color:#333}
.stars{margin-top:2px;color:var(--gold);font-size:15px;letter-spacing:2px}
.price{margin-top:2px;font:700 17px "Lato",sans-serif}
.price s{font:400 12px "Lato",sans-serif;color:#888;margin-left:4px}
.member{top:2740px;width:243px;text-align:center}
.member-img{width:243px;height:265px}
.member h3{margin-top:28px;font:900 14.5px "Lato",sans-serif}
.member p{margin-top:8px;font:400 13.5px/24px "Poppins",sans-serif;color:#333}
.post{top:3324px;width:243px}
.post-img{width:243px;height:197px}
.post h3{margin-top:18px;width:215px;font:500 18.5px/28px "Lato",sans-serif;color:var(--ink)}
.post p{margin-top:10px;font:400 13.5px/25px "Poppins",sans-serif;color:#333}
.outline-btn{left:512px;top:3742px;width:178px;height:51px;border:2px solid var(--line);display:flex;align-items:center;justify-content:center;font:500 18px "Lato",sans-serif}
.contact{left:74px;top:3879px;width:1052px;height:479px;background:var(--panel)}
.field{position:absolute;background:var(--white);font:400 14px "Poppins",sans-serif;color:#444;padding:14px 18px}
.news-label{left:103px;top:4514px;font:400 22px "Lato",sans-serif}
.news-input{left:424px;top:4496px;width:470px;height:67px;border:1.5px solid #bbb;font:400 15px "Poppins",sans-serif;color:#444;padding:22px 16px}
.fcol{top:4700px}
.fcol h4{font:700 19px "Lato",sans-serif;margin-bottom:14px}
.fcol li{list-style:none;font:400 16px/34px "Lato",sans-serif;color:#444;white-space:nowrap}
.social{top:4858px;width:37px;height:37px;border-radius:50%}
.pay{top:4986px;width:44px;height:18px;border-radius:3px;background:#c9c9c9}
.copy{left:0;top:5099px;width:1200px;height:78px;background:var(--panel);text-align:center;font:400 14px/78px "Lato",sans-serif;color:#444}
</style>
</head>
<body>

<div class="abs topbar"><span>GET 20% OFF SALE EVERYTHING + FREE SHIPPING&nbsp; SEE DETAILS</span><span>My Account &nbsp;/&nbsp; Sign in or Create an account</span></div>

<div class="abs brand">Bold Dawn</div>
<nav class="abs nav"><span>HOME</span><span>ABOUT US</span><span>PRODUCTS</span><span>BLOG</span><span>CONTACT US</span></nav>
<div class="abs icon-btn outline" style="left:973px"><svg width="18" height="18" viewBox="0 0 18 18"><circle cx="7.5" cy="7.5" r="5.5" fill="none" stroke="#1e1e1e" stroke-width="2.4"/><line x1="11.5" y1="11.5" x2="16" y2="16" stroke="#1e1e1e" stroke-width="2.6"/></svg></div>
<div class="abs icon-btn solid" style="left:1027px"><svg width="20" height="18" viewBox="0 0 20 18"><path d="M1 6h18l-2 10H3z" fill="#fff"/><path d="M6 6l4-5 4 5" fill="none" stroke="#fff" stroke-width="1.6"/></svg></div>
<div class="abs icon-btn solid" style="left:1081px"><svg width="18" height="14" viewBox="0 0 18 14"><rect y="0" width="18" height="2.4" fill="#fff"/><rect y="5.8" width="18" height="2.4" fill="#fff"/><rect y="11.6" width="18" height="2.4" fill="#fff"/></svg></div>

<section class="abs hero" role="img" aria-label="Smiling man in a black polo shirt talking on a phone"></section>
<div class="abs hero-name">Bold Dawn</div>
<div class="abs hero-sub">APPAREL</div>
<div class="abs hero-copy">Sed ut perspiciatis unde omnis iste<br>natus error sit voluptatem</div>
<div class="abs btn" style="left:74px;top:651px;width:159px;height:45px;background:var(--dark)">SHOP NOW</div>
<div class="abs dot" style="left:76px;background:#fff"></div>
<div class="abs dot" style="left:95px"></div>
<div class="abs dot" style="left:114px"></div>
<div class="abs dot" style="left:133px"></div>

<div class="abs cat" style="left:74px"><div class="cat-img" role="img" aria-label="Grey crew-neck t-shirt" style="background:radial-gradient(circle,#8c8c8c 0%,#a8a8a8 55%,#f2f2f2 72%)"></div><div class="cat-title">NEMO ENIM<br>IPSAM</div><div class="cat-link">SHOP NOW</div></div>
<div class="abs cat" style="left:430px"><div class="cat-img" role="img" aria-label="Navy blue polo shirt" style="background:radial-gradient(circle,#1e2f7a 0%,#233a8e 55%,#f2f2f2 72%)"></div><div class="cat-title">NEMO ENIM<br>IPSAM</div><div class="cat-link">SHOP NOW</div></div>
<div class="abs cat" style="left:784px"><div class="cat-img" role="img" aria-label="Green v-neck t-shirt" style="background:radial-gradient(circle,#1f5a4a 0%,#2e6b5a 55%,#f2f2f2 72%)"></div><div class="cat-title">NEMO ENIM<br>IPSAM</div><div class="cat-link">SHOP NOW</div></div>

<div class="abs mv" style="left:74px"><h2>MISSION</h2><p>“ Sed ut perspiciatis unde omnis iste natus error sit voluptatem accusantium doloremque laudantium, totam rem aperiam, eaque ipsa quae ab illo inventore veritatis et quasi architecto beata..”</p></div>
<div class="abs mv" style="left:607px"><h2>VISION</h2><p>“ Sed ut perspiciatis unde omnis iste natus error sit voluptatem accusantium doloremque laudantium, totam rem aperiam, eaque ipsa quae ab illo inventore veritatis et quasi architecto beata..”</p></div>

<section class="abs about">
  <h2>ABOUT BOLD DAWN APPAREL</h2>
  <p>Sed ut perspiciatis unde omnis iste natus error sit voluptatem accusantium doloremque laudantium, totam rem aperiam, eaque ipsa quae ab illo inventore veritatis et quasi architecto beatae vitae dicta sunt explicabo. Nemo enim ipsam voluptatem quia voluptas sit aspernatur aut odit aut fugit, sed quia consequuntur magni dolores eos qui ratione.</p>
  <div class="btn">READ MORE</div>
  <div class="about-mark">Bold Dawn</div>
</section>

<h2 class="abs sec-title" style="top:2048px">OUR PRODUCTS</h2>
<div class="abs prod" style="left:74px"><div class="prod-img"><div class="shape" role="img" aria-label="Navy polo shirt" style="background:radial-gradient(circle,#1c2540 0%,#2a3558 60%,#f2f2f2 75%)"></div><div class="sale">SALE</div></div><div class="prod-name">PRODUCT NAME</div><div class="prod-sub">Malesuada fames lorem</div><div class="stars">★★★★★</div><div class="price">$14.99<s>$23.99</s></div></div>
<div class="abs prod" style="left:344px"><div class="prod-img"><div class="shape" role="img" aria-label="Orange turtleneck top" style="background:radial-gradient(circle,#e9a158 0%,#eeab62 60%,#f2f2f2 75%)"></div></div><div class="prod-name">PRODUCT NAME</div><div class="prod-sub">Malesuada fames lorem</div><div class="stars">★★★★★</div><div class="price">$14.99<s>$23.99</s></div></div>
<div class="abs prod" style="left:615px"><div class="prod-img"><div class="shape" role="img" aria-label="Black polo shirt" style="background:radial-gradient(circle,#1a1a1a 0%,#2a2a2a 60%,#f2f2f2 75%)"></div><div class="sale">SALE</div></div><div class="prod-name">PRODUCT NAME</div><div class="prod-sub">Malesuada fames lorem</div><div class="stars">★★★★★</div><div class="price">$14.99<s>$23.99</s></div></div>
<div class="abs prod" style="left:884px"><div class="prod-img"><div class="shape" role="img" aria-label="Pink t-shirt" style="background:radial-gradient(circle,#e5579a 0%,#ea68a6 60%,#f2f2f2 75%)"></div></div><div class="prod-name">PRODUCT NAME</div><div class="prod-sub">Malesuada fames lorem</div><div class="stars">★★★★★</div><div class="price">$14.99<s>$23.99</s></div></div>

<div class="abs rule" style="top:2602px"></div>

<h2 class="abs sec-title" style="top:2662px">OUR TEAM</h2>
<div class="abs member" style="left:74px"><div class="member-img" role="img" aria-label="Team member portrait, older man in a knit sweater" style="background:linear-gradient(180deg,#e4e4e4,#bdb6ab)"></div><h3>NAME HEADING</h3><p>Excepteur sint occaecat cupidatat non proident eiusmod.</p></div>
<div class="abs member" style="left:344px"><div class="member-img" role="img" aria-label="Team member portrait, man in a light blue polo" style="background:linear-gradient(180deg,#dcdcdc,#a9cfe0)"></div><h3>NAME HEADING</h3><p>Excepteur sint occaecat cupidatat non proident eiusmod.</p></div>
<div class="abs member" style="left:615px"><div class="member-img" role="img" aria-label="Team member portrait, woman in a blue sweater" style="background:linear-gradient(180deg,#d8c9c2,#7f9fd0)"></div><h3>NAME HEADING</h3><p>Excepteur sint occaecat cupidatat non proident eiusmod.</p></div>
<div class="abs member" style="left:884px"><div class="member-img" role="img" aria-label="Team member portrait, man in a white sweater at home" style="background:linear-gradient(180deg,#d9d3cc,#ece9e5)"></div><h3>NAME HEADING</h3><p>Excepteur sint occaecat cupidatat non proident eiusmod.</p></div>

<div class="abs rule" style="top:3175px"></div>

<h2 class="abs sec-title" style="top:3240px">BLOG POSTS</h2>
<div class="abs post" style="left:74px"><div class="post-img" role="img" aria-label="Woman in black t-shirt against a brick wall" style="background:linear-gradient(90deg,#e8e8e8,#8a8a8a 50%,#3a3a3a)"></div><h3>Sed ut perspiciatis unde omnis iste natus</h3><p>Nemo enim ipsam voluptatem quia voluptas sit aspernatur aut odit aut fugit, sed quia consequ.</p></div>
<div class="abs post" style="left:344px"><div class="post-img" role="img" aria-label="Rack of colourful t-shirts on hangers" style="background:linear-gradient(90deg,#c9433e,#e0a03c 25%,#3fa2a8 50%,#3856a6 75%,#b04070)"></div><h3>Sed ut perspiciatis unde omnis iste natus</h3><p>Nemo enim ipsam voluptatem quia voluptas sit aspernatur aut odit aut fugit, sed quia consequ.</p></div>
<div class="abs post" style="left:615px"><div class="post-img" role="img" aria-label="White t-shirt on green leaves" style="background:radial-gradient(circle,#f4f4f4 0%,#e6eee0 30%,#3f7a34 60%,#2d5a26)"></div><h3>Sed ut perspiciatis unde omnis iste natus</h3><p>Nemo enim ipsam voluptatem quia voluptas sit aspernatur aut odit aut fugit, sed quia consequ.</p></div>
<div class="abs post" style="left:884px"><div class="post-img" role="img" aria-label="Woman in grey t-shirt outdoors by a waterfall" style="background:linear-gradient(180deg,#6f7d6a,#8f9490 50%,#6a6258)"></div><h3>Sed ut perspiciatis unde omnis iste natus</h3><p>Nemo enim ipsam voluptatem quia voluptas sit aspernatur aut odit aut fugit, sed quia consequ.</p></div>
<div class="abs outline-btn">View All Posts</div>

<section class="abs contact">
  <h2 class="abs sec-title" style="left:0;width:1052px;top:62px">GET IN TOUCH WITH US</h2>
  <div class="field" style="left:91px;top:137px;width:428px;height:50px">Enter Name</div>
  <div class="field" style="left:91px;top:205px;width:428px;height:50px">Email Address</div>
  <div class="field" style="left:91px;top:272px;width:428px;height:50px">Phone No</div>
  <div class="field" style="left:533px;top:137px;width:428px;height:185px">Message</div>
  <div class="abs btn" style="left:449px;top:350px;width:156px;height:46px">SUBMIT</div>
</section>

<div class="abs rule" style="left:0;width:1200px;top:4427px;height:1px"></div>
<div class="abs news-label">Subscribe to Our Newsletter</div>
<div class="abs news-input">Email Address</div>
<div class="abs btn" style="left:906px;top:4496px;width:194px;height:67px;font:500 21px 'Lato',sans-serif">Subscribe</div>
<div class="abs rule" style="left:0;width:1200px;top:4629px;height:1px"></div>

<div class="abs fcol" style="left:74px"><h4>Site Map</h4><ul><li>Sed ut perspiciatis</li><li>Unde omnis iste</li><li>Natus error sit volu</li><li>Ptatem accu</li><li>Santium doloremque</li><li>Laudantium</li></ul></div>
<div class="abs fcol" style="left:342px"><h4>Our Categories</h4><ul><li>Sed ut perspiciatis</li><li>Unde omnis iste</li><li>Natus error sit volu</li><li>Ptatem accu</li><li>Santium doloremque</li><li>Laudantium</li></ul></div>
<div class="abs fcol" style="left:615px"><h4>Customer Support</h4><ul><li>Sed ut perspiciatis</li><li>Unde omnis iste</li><li>Natus error sit volu</li><li>Ptatem accu</li><li>Santium doloremque</li><li>Laudantium</li></ul></div>
<div class="abs fcol" style="left:882px"><h4>Contact Us</h4><ul><li style="font-size:15px">+1-555-014-2290</li><li style="font-size:15px">hello@bolddawnapperal.com</li></ul></div>
<div class="abs sans" style="left:886px;top:4812px;font:700 19px 'Lato',sans-serif">Get in Touch</div>
<div class="abs social" style="left:886px;background:#1da1f2"></div>
<div class="abs social" style="left:932px;background:#3b5998"></div>
<div class="abs social" style="left:980px;background:#cb2027"></div>
<div class="abs social" style="left:1027px;background:#e62117"></div>
<div class="abs social" style="left:1075px;background:#1e88d4"></div>
<div class="abs sans" style="left:886px;top:4938px;font:700 19px 'Lato',sans-serif">Payment</div>
<div class="abs pay" style="left:886px"></div>
<div class="abs pay" style="left:936px"></div>
<div class="abs pay" style="left:986px"></div>
<div class="abs pay" style="left:1036px"></div>
<div class="abs pay" style="left:1086px;width:38px"></div>
<div class="abs pay" style="left:886px;top:5018px"></div>
<div class="abs pay" style="left:936px;top:5018px"></div>
<div class="abs pay" style="left:986px;top:5018px"></div>
<div class="abs pay" style="left:1036px;top:5018px"></div>

<footer class="abs copy">Copyright 2023 Company Name. All Rights Reserved</footer>
</body>
</html>
```